Tolvik Commercial Cleaning is lookong for a new business card design.

A fresh new design that's professional and stylish. We need a serious upgrade to our business cards. I have included pictures of our existing ones. Our clients include professional individuals and business owners. We woupdblike something professional and upbeat. Please have fun and see what you come uo with.

Target Market(s)

Property managers, business owners, facility managers and other similar professionals

Industry/Entity Type

Janitorial

Contact Information for Business Card

Name, cell, office number, email, web address

Font styles to use
Sans Serif

Colors

Designer to choose colors to be used in the design.

Requirements
Must have
• please use the green color in our logo
Nice to have
• Bar code
Should not have
• Address

```html
<!DOCTYPE html>
<html lang="en">
<head>
<meta charset="utf-8">
<title>Tolvik Commercial Cleaning – Business Card</title>
<link href="https://fonts.googleapis.com/css2?family=Montserrat:wght@400;500;700&display=swap" rel="stylesheet">
<style>
  :root {
    --backdrop: #2e2f31;
    --card: #ffffff;
    --card-shade: #ececec;
    --brand-green: #3bb05a;
    --brand-blue: #2f65a0;
    --text-grey: #7b7b7b;
    --white: #ffffff;
  }
  * { box-sizing: border-box; margin: 0; padding: 0; }
  html, body {
    width: 1200px; height: 1200px; overflow: hidden;
    background: var(--backdrop);
    font-family: "Montserrat", sans-serif;
  }
  .canvas {
    width: 1200px; height: 1200px;
    display: flex; flex-direction: column; align-items: center; justify-content: center;
    gap: 60px;
  }
  .card {
    position: relative;
    width: 840px; height: 480px;
    background: linear-gradient(135deg, var(--card) 0%, var(--card) 45%, var(--card-shade) 100%);
    overflow: hidden;
    box-shadow: 0 10px 30px rgba(0,0,0,0.45);
  }
  /* Name side */
  .card--brand { display: flex; align-items: center; justify-content: center; }
  .brand-name {
    font-weight: 700; font-size: 120px; letter-spacing: -2px;
    color: var(--brand-green);
  }
  /* Contact side */
  .swoosh { position: absolute; inset: 0; width: 100%; height: 100%; }
  .holder-name {
    position: absolute; left: 150px; top: 150px;
    font-weight: 700; font-size: 34px; color: var(--brand-blue);
  }
  .divider {
    position: absolute; left: 420px; top: 215px;
    width: 3px; height: 80px; background: var(--brand-green);
  }
  .contact-list {
    position: absolute; left: 445px; top: 212px;
    list-style: none;
    font-size: 21px; font-weight: 400; color: var(--text-grey);
  }
  .contact-item { display: flex; align-items: center; gap: 10px; line-height: 29px; }
  .contact-icon { width: 16px; height: 16px; fill: var(--brand-blue); flex: none; }
  .tagline {
    position: absolute; right: 40px; bottom: 18px;
    font-size: 22px; font-weight: 400; color: var(--white);
  }
</style>
</head>
<body>
<main class="canvas">
  <section class="card card--brand">
    <span class="brand-name">Tolvik</span>
  </section>

  <section class="card card--contact">
    <svg class="swoosh" viewBox="0 0 840 480" preserveAspectRatio="none" aria-hidden="true">
      <path d="M0,222 C180,228 420,320 560,410 C420,330 200,256 0,240 Z" fill="var(--brand-green)"/>
      <path d="M0,256 C260,300 560,440 840,380 L840,480 L0,480 Z" fill="var(--brand-blue)"/>
    </svg>

    <h1 class="holder-name">Marcus Delane</h1>
    <div class="divider"></div>
    <ul class="contact-list">
      <li class="contact-item">
        <svg class="contact-icon" viewBox="0 0 16 16"><path d="M3.5 1l2.5 3-1.5 1.5c.8 2 2.5 3.7 4.5 4.5L10.5 8.5l3 2.5-1.5 3C7 14 2 9 2 2.5z"/></svg>
        (555) 014-2870
      </li>
      <li class="contact-item">
        <svg class="contact-icon" viewBox="0 0 16 16"><path d="M1 3h14v10H1z M1 3l7 6 7-6" stroke="var(--white)" stroke-width="1"/></svg>
        marcus@tolvikcleaning.com
      </li>
      <li class="contact-item">
        <svg class="contact-icon" viewBox="0 0 16 16"><circle cx="8" cy="8" r="7"/><path d="M1 8h14M8 1c-3 3-3 11 0 14M8 1c3 3 3 11 0 14" stroke="var(--white)" stroke-width="1" fill="none"/></svg>
        www.tolvikcleaning.com
      </li>
    </ul>
    <p class="tagline">Spotless Spaces Every Day</p>
  </section>
</main>
</body>
</html>
```